Professional & attention grabbing.

A business card design, front and back. I already have a logo I will attach, but I am open to something new as well.
Things to include:
Name:
Title:
Phone:
Email:
Wanting something that is professional but attention grabbing.
Also we do a lot of work using drones on natural gas pipelines (leading the future)if you want to include any of that. I'm open to ideas.
Target Market(s)
Natural gas transmission industry / greenhouse gas mitigation industry
Industry/Entity Type
Business
Colors
Designer to choose colors to be used in the design.
Look and feel
Each slider illustrates characteristics of the customer's brand and the style your logo design should communicate.

```html
<!DOCTYPE html>
<html lang="en">
<head>
<meta charset="UTF-8">
<title>KV Field Inspections – Business Card</title>
<link rel="stylesheet" href="https://fonts.googleapis.com/css2?family=Rajdhani:wght@500;600;700&display=swap">
<style>
  :root {
    --page-bg: #d9dbdd;
    --card-bg: #eef0f1;
    --brand-red: #b0252a;
    --brand-red-dark: #8f1c21;
    --ink: #231f20;
    --text-grey: #3a3a3a;
  }
  * { margin: 0; padding: 0; box-sizing: border-box; }
  html, body {
    width: 1200px;
    height: 969px;
    overflow: hidden;
    background: var(--page-bg);
  }
  .business-card {
    position: absolute;
    left: 75px;
    top: 186px;
    width: 1050px;
    height: 596px;
    border-radius: 36px;
    background: var(--card-bg);
    overflow: hidden;
    font-family: "Rajdhani", sans-serif;
    box-shadow: 0 10px 30px rgba(0,0,0,0.12);
  }
  .accent-band {
    position: absolute;
    top: 0;
    right: 0;
    width: 150px;
    height: 100%;
    background: linear-gradient(180deg, var(--brand-red), var(--brand-red-dark));
  }
  .accent-rule {
    position: absolute;
    top: 0;
    right: 170px;
    width: 10px;
    height: 100%;
    background: var(--ink);
  }
  .brand-lockup {
    position: absolute;
    left: 58px;
    top: 96px;
    display: flex;
    align-items: center;
    gap: 20px;
  }
  .brand-square {
    width: 62px;
    height: 62px;
    background: var(--brand-red);
  }
  .brand-name {
    font-size: 48px;
    font-weight: 700;
    color: var(--ink);
    line-height: 1;
    letter-spacing: 0.5px;
  }
  .person-name {
    position: absolute;
    left: 58px;
    top: 288px;
    font-size: 40px;
    font-weight: 700;
    color: var(--brand-red);
    letter-spacing: 1px;
  }
  .person-title {
    position: absolute;
    left: 58px;
    top: 338px;
    font-size: 32px;
    font-weight: 500;
    color: var(--text-grey);
  }
  .contact-list {
    position: absolute;
    left: 58px;
    top: 412px;
    list-style: none;
  }
  .contact-item {
    display: flex;
    align-items: center;
    gap: 14px;
    height: 41px;
    font-size: 30px;
    font-weight: 500;
    color: var(--text-grey);
  }
  .contact-icon {
    width: 22px;
    height: 22px;
    fill: var(--brand-red);
    flex: none;
  }
</style>
</head>
<body>
  <div class="business-card">
    <div class="accent-rule"></div>
    <div class="accent-band"></div>

    <div class="brand-lockup">
      <div class="brand-square"></div>
      <div class="brand-name">KV Field Inspections</div>
    </div>

    <div class="person-name">DANIEL REYES</div>
    <div class="person-title">CEO/Founder</div>

    <ul class="contact-list">
      <li class="contact-item">
        <svg class="contact-icon" viewBox="0 0 24 24"><path d="M6.6 10.8a15.1 15.1 0 0 0 6.6 6.6l2.2-2.2a1 1 0 0 1 1-.25 11.4 11.4 0 0 0 3.6.57 1 1 0 0 1 1 1V20a1 1 0 0 1-1 1A17 17 0 0 1 3 4a1 1 0 0 1 1-1h3.5a1 1 0 0 1 1 1c0 1.25.2 2.450.57 3.57a1 1 0 0 1-.25 1z"/></svg>
        <span>555 210 4873</span>
      </li>
      <li class="contact-item">
        <svg class="contact-icon" viewBox="0 0 24 24"><path d="M2 5h20v14H2z"/><path d="M2 6.5l10 7.5 10-7.5V5H2z" fill="#eef0f1"/></svg>
        <span>hello@kvfield.com</span>
      </li>
      <li class="contact-item">
        <svg class="contact-icon" viewBox="0 0 24 24"><circle cx="12" cy="12" r="10"/><path d="M2 12h20M12 2c3 3 3 17 0 20M12 2c-3 3-3 17 0 20" stroke="#eef0f1" stroke-width="1.6" fill="none"/></svg>
        <span>www.kvfield.com</span>
      </li>
    </ul>
  </div>
</body>
</html>
```